Business Card for Vorla Parts Wholesale supplier

Hi There! I need a new business card for our company. We are specialized in selling Vorla parts, mostly we sell new LCD screens for Zelnar and Drelks. I would like to see that back in the design.

You can find the colors and logo's on our website: www.hartuvo.nl

Industry/Entity Type

Business

Contact Information for Business Card

My Details:
Tobias Lindqvist

Phone: 0031687203316
E-mail: Tobias@hartuvo.nl

Slogan: "Because Quality Matters"

Font styles to use
Sans Serif

Colors

Designer to choose colors to be used in the design.

Requirements
Must have
• A Black backside with the Hartuvo logo on it. The front side should be clean with only my contact details.
• But I'm also open for something really different or awesome!
Nice to have
• Remember that we are in the parts & repairing industry, So i'll be handing those business cards mainly to repair companies. Maybe you can do something with that thought :)

```html
<!DOCTYPE html>
<html lang="en">
<head>
<meta charset="utf-8">
<title>Hartuvo Business Card</title>
<link href="https://fonts.googleapis.com/css2?family=Open+Sans:wght@400;600;800&display=swap" rel="stylesheet">
<style>
  :root {
    --bg: #ececec;
    --card-white: #ffffff;
    --card-black: #2a2a2a;
    --accent: #f26a1b;
    --ink: #1a1a1a;
    --ink-soft: #3a3a3a;
    --on-dark: #ffffff;
  }
  * { box-sizing: border-box; margin: 0; padding: 0; }
  html, body {
    width: 1200px; height: 900px; overflow: hidden;
    background: var(--bg);
    font-family: "Open Sans", Arial, sans-serif;
  }
  .canvas {
    position: relative; width: 1200px; height: 900px;
  }
  .card {
    position: absolute; left: 320px; width: 560px; height: 320px;
    border-radius: 4px;
    box-shadow: 0 6px 18px rgba(0,0,0,0.12);
    overflow: hidden;
  }
  .card--front { top: 100px; background: var(--card-white); }
  .card--back  { top: 480px; background: var(--card-black); }

  /* brand name */
  .brand { display: flex; align-items: center; gap: 12px; }
  .brand__mark { width: 34px; height: 34px; background: var(--accent); border-radius: 4px; }
  .brand__name { font-weight: 800; font-size: 46px; letter-spacing: 1px; line-height: 1; }

  /* front */
  .card--front .brand { position: absolute; left: 36px; top: 36px; }
  .card--front .brand__name { color: var(--ink); }
  .contact { position: absolute; left: 40px; top: 112px; }
  .contact__name {
    color: var(--accent); font-weight: 600; font-size: 17px;
    text-transform: uppercase; letter-spacing: 1px; margin-bottom: 8px;
  }
  .contact__list { list-style: none; }
  .contact__item {
    display: flex; align-items: center; gap: 8px;
    font-size: 12.5px; color: var(--ink-soft); line-height: 20px;
  }
  .contact__icon { width: 11px; height: 11px; fill: var(--accent); flex: none; }
  .contact__slogan {
    color: var(--accent); font-weight: 600; font-size: 13px;
    text-transform: uppercase; letter-spacing: 0.5px; margin-top: 8px;
  }
  .product-visual {
    position: absolute; right: 30px; top: 110px; width: 230px; height: 185px;
    border-radius: 10px;
    background: linear-gradient(135deg, #f3f3f3 0%, #d8d8d8 45%, #2b2b2b 46%, #3c3c3c 60%, #c9c9c9 61%, #e8e8e8 100%);
  }

  /* back */
  .card--back .brand {
    position: absolute; left: 0; right: 0; top: 110px; justify-content: center;
  }
  .card--back .brand__name { color: var(--on-dark); font-size: 58px; }
  .card--back .brand__mark { width: 42px; height: 42px; }
  .tagline {
    position: absolute; left: 0; right: 0; top: 200px; text-align: center;
    color: var(--on-dark); font-weight: 600; font-size: 17px; letter-spacing: 0.3px;
  }
  .tagline__divider { margin: 0 12px; }
</style>
</head>
<body>
<main class="canvas">
  <section class="card card--front" aria-label="Business card front">
    <div class="brand">
      <span class="brand__mark"></span>
      <span class="brand__name">hartuvo</span>
    </div>
    <div class="contact">
      <p class="contact__name">Tobias Lindqvist</p>
      <ul class="contact__list">
        <li class="contact__item">
          <svg class="contact__icon" viewBox="0 0 24 24"><path d="M6.6 10.8a15.1 15.1 0 0 0 6.6 6.6l2.2-2.2c.3-.3.7-.4 1-.2 1.1.4 2.3.6 3.6.6.6 0 1 .4 1 1V20c0 .6-.4 1-1 1A17 17 0 0 1 3 4c0-.6.4-1 1-1h3.5c.6 0 1 .4 1 1 0 1.3.2 2.5.6 3.6.1.3 0 .7-.2 1z"/></svg>
          0031687203316
        </li>
        <li class="contact__item">
          <svg class="contact__icon" viewBox="0 0 24 24"><path d="M2 5h20v14H2z M2 5l10 8 10-8" /></svg>
          Tobias@hartuvo.nl
        </li>
        <li class="contact__item">
          <svg class="contact__icon" viewBox="0 0 24 24"><circle cx="12" cy="12" r="10"/></svg>
          www.hartuvo.nl
        </li>
      </ul>
      <p class="contact__slogan">Because Quality Matters</p>
    </div>
    <div class="product-visual" role="img" aria-label="Photo of a white Zelnar replacement LCD screen front and its metal back assembly"></div>
  </section>

  <section class="card card--back" aria-label="Business card back">
    <div class="brand">
      <span class="brand__mark"></span>
      <span class="brand__name">hartuvo</span>
    </div>
    <p class="tagline">The highest quality<span class="tagline__divider">|</span>OEM parts</p>
  </section>
</main>
</body>
</html>
```